professional business card design

Business card design. Photos have been uploaded and i am open to the designer choosing which photos to use. Would like the card to be mostyly in a grey scale design with black, whites, silver & grey colours. I have added copy of our flyer as would like on the back side of card our services to be listed. Do not use any bright colurs such as blue red green or yellow. i need to be able to edit the phone number and naem in the final card design submitted.

Target Market(s)

Clients

Industry/Entity Type

earhmovibng and transport

Contact Information for Business Card

Director Name, address, email, phone number and services

Colors

Designer to choose only greyscale colors for use in the design.

Requirements
Should not have
• no yellow, red, blue or green

```html
<!DOCTYPE html>
<html lang="en">
<head>
<meta charset="utf-8">
<title>KRV Pty Ltd – Business Card</title>
<link rel="stylesheet" href="https://fonts.googleapis.com/css2?family=Bebas+Neue&family=Montserrat:wght@400;500;600&display=swap">
<style>
  :root {
    --canvas: #d9d9d9;
    --card-black: #0b0b0b;
    --card-graphite: #2a2a2a;
    --mesh-light: #505050;
    --steel: #8a8a8a;
    --silver: #cfcfcf;
    --paper: #f4f4f4;
    --ink: #111111;
    --white: #ffffff;
  }
  * { box-sizing: border-box; margin: 0; padding: 0; }
  html, body { width: 1200px; height: 1200px; overflow: hidden; }
  body {
    background: var(--canvas);
    font-family: "Montserrat", sans-serif;
    position: relative;
  }
  .card {
    position: absolute;
    left: 150px;
    width: 900px;
    height: 515px;
    border-radius: 34px;
    overflow: hidden;
    box-shadow: 0 10px 30px rgba(0,0,0,.35);
  }
  .card--back { top: 60px; display: flex; }
  .card--front { top: 625px; background: var(--card-black); }

  .mesh-texture {
    position: absolute;
    inset: 0;
    background:
      radial-gradient(ellipse 60% 70% at 42% 30%, var(--mesh-light) 0%, var(--card-graphite) 45%, var(--card-black) 90%);
  }

  /* back: contact panel */
  .contact-panel {
    position: relative;
    width: 50%;
    color: var(--white);
    padding: 0 36px 58px 48px;
    display: flex;
    flex-direction: column;
    justify-content: flex-end;
  }
  .contact-panel .mesh-texture {
    background: radial-gradient(ellipse 70% 60% at 55% 35%, #5a5a5a 0%, var(--card-graphite) 45%, var(--card-black) 90%);
  }
  .contact-content { position: relative; }
  .contact-name {
    font-size: 40px;
    font-weight: 500;
    letter-spacing: 1px;
    line-height: 1;
    border-left: 4px solid var(--white);
    padding-left: 12px;
  }
  .contact-role {
    font-size: 18px;
    letter-spacing: 1px;
    color: var(--silver);
    padding-left: 16px;
    margin: 6px 0 26px;
  }
  .contact-list { list-style: none; font-size: 18px; line-height: 1.5; }
  .contact-list li { display: flex; align-items: flex-start; gap: 12px; }
  .contact-list svg { width: 20px; height: 20px; flex: none; margin-top: 4px; fill: var(--white); }

  .divider { width: 16px; background: linear-gradient(90deg, var(--steel), var(--silver)); }

  /* back: services panel */
  .services-panel {
    flex: 1;
    background: linear-gradient(160deg, var(--white), var(--paper) 60%, #e4e4e4);
    color: var(--ink);
    padding: 92px 30px 0 56px;
    font-family: "Bebas Neue", sans-serif;
  }
  .services-title { font-size: 38px; font-weight: 400; letter-spacing: 1px; margin-bottom: 6px; }
  .services-list { list-style: none; font-size: 22px; line-height: 1.08; letter-spacing: .5px; }
  .services-list li::before { content: "• "; }
  .services-list .cont { padding-left: 12px; }
  .services-list .cont::before { content: ""; }

  /* front */
  .brand-name {
    position: absolute;
    top: 95px;
    left: 215px;
    color: var(--silver);
    font-family: "Montserrat", sans-serif;
    font-weight: 600;
    font-size: 78px;
    letter-spacing: 3px;
    line-height: 1;
  }
  .truck-photo {
    position: absolute;
    left: 190px;
    right: 0;
    top: 215px;
    bottom: 0;
    background:
      linear-gradient(90deg, var(--card-black) 0%, rgba(11,11,11,0) 30%),
      linear-gradient(180deg, rgba(11,11,11,0) 0%, rgba(11,11,11,.2) 60%, var(--card-black) 100%),
      linear-gradient(100deg, #3a3a3a 0%, #6a6a6a 45%, #9a9a9a 65%, #5a5a5a 85%, #2a2a2a 100%);
  }
</style>
</head>
<body>
  <section class="card card--back" aria-label="Card back">
    <div class="contact-panel">
      <div class="mesh-texture" role="img" aria-label="Dark perforated metal mesh texture"></div>
      <div class="contact-content">
        <h1 class="contact-name">JOHN DOE</h1>
        <p class="contact-role">CEO | FOUNDER</p>
        <ul class="contact-list">
          <li><svg viewBox="0 0 24 24"><path d="M6.6 10.8a15 15 0 0 0 6.6 6.6l2.2-2.2a1 1 0 0 1 1-.25 11.4 11.4 0 0 0 3.6.57 1 1 0 0 1 1 1V20a1 1 0 0 1-1 1A17 17 0 0 1 3 4a1 1 0 0 1 1-1h3.5a1 1 0 0 1 1 1c0 1.25.2 2.45.57 3.57a1 1 0 0 1-.25 1z"/></svg>(000) 000 0000</li>
          <li><svg viewBox="0 0 24 24"><path d="M2 5h20v14H2z M3 6l9 7 9-7" fill="none" stroke="#fff" stroke-width="2"/></svg>email@youremail.com</li>
          <li><svg viewBox="0 0 24 24"><circle cx="12" cy="12" r="9" fill="none" stroke="#fff" stroke-width="2"/><path d="M3 12h18M12 3c3 3 3 15 0 18M12 3c-3 3-3 15 0 18" fill="none" stroke="#fff" stroke-width="1.6"/></svg>www.yourwebsite.com</li>
          <li><svg viewBox="0 0 24 24"><path d="M12 2a7 7 0 0 0-7 7c0 5 7 13 7 13s7-8 7-13a7 7 0 0 0-7-7zm0 9.5A2.5 2.5 0 1 1 12 6.5a2.5 2.5 0 0 1 0 5z"/></svg>KRV Pty Ltd | Depot: Lot 41,<br>Ridgeway Road Millbrook</li>
        </ul>
      </div>
    </div>
    <div class="divider"></div>
    <div class="services-panel">
      <h2 class="services-title">Our Services</h2>
      <ul class="services-list">
        <li>Over Size Loads / Hot Shot Loads</li>
        <li>Heavy Vehicle Recovery Services</li>
        <li>Potable Water Deliveries</li>
        <li>Road Building / Maintenance</li>
        <li>Earthworks</li>
        <li>Sand &amp; Metal Supply &amp; Cartage</li>
        <li>Road Train Tippers</li>
        <li>Road Train Tankers</li>
        <li>Road Train Flat Tops</li>
        <li>Drop Deck Trailers</li>
        <li>Mine Site Accredited</li>
        <li class="cont">Equipment &amp; Operators</li>
      </ul>
    </div>
  </section>

  <section class="card card--front" aria-label="Card front">
    <div class="mesh-texture" role="img" aria-label="Dark perforated metal mesh texture"></div>
    <div class="truck-photo" role="img" aria-label="Greyscale photo of road train trucks"></div>
    <p class="brand-name">KRV Pty Ltd</p>
  </section>
</body>
</html>
```